Brookvane Consulting Business Card Design

Business Card Design for Brookvane Consulting. Brookvane Consulting is a boutique consultancy based in Atlanta, GA., that specializes in marketing strategy, organization planning, and leadership development. We provide solutions for small businesses and startups as well as Vantage 300 companies.

http://brookvaneconsulting.com/

Target Market(s)

We provide solutions for small businesses and startups as well as Vantage 300 companies.

Industry/Entity Type

Consulting

Contact Information for Business Card

Two sided business card with priority on contact information, logo, tag line (Clear Plans, Strong Leaders, Lasting Growth)

Colors

Designer to choose colors to be used in the design.

Requirements
Must have
• contact information, logo, tag line (Clear Plans, Strong Leaders, Lasting Growth)
• Simple no over communication.
Nice to have
• I would like to see different placements of logo and creative use of both sides of the card
Should not have
• Do not put too much information on the card.

```html
<!DOCTYPE html>
<html lang="en">
<head>
<meta charset="utf-8">
<title>Brookvane Consulting – Business Card</title>
<link rel="stylesheet" href="https://fonts.googleapis.com/css2?family=Open+Sans:wght@400;700&display=swap">
<style>
  :root {
    --backdrop: #2b2b2b;
    --card: #343434;
    --panel: #0a0a0a;
    --rule: #8c8c8c;
    --ink: #ffffff;
    --ink-soft: #e6e6e6;
  }
  * { margin: 0; padding: 0; box-sizing: border-box; }
  html, body { width: 799px; height: 1200px; overflow: hidden; }
  body {
    background: var(--backdrop);
    font-family: "Open Sans", Arial, sans-serif;
    color: var(--ink);
    position: relative;
  }
  .card {
    position: absolute;
    left: 80px;
    width: 640px;
    height: 366px;
    border-radius: 26px;
    background: var(--card);
    overflow: hidden;
    box-shadow: 0 14px 30px rgba(0,0,0,.45);
  }
  .card--front { top: 150px; }
  .card--back { top: 670px; }

  .wordmark { display: flex; align-items: center; gap: 14px; }
  .wordmark__square { width: 18px; height: 18px; background: var(--ink); flex: none; }
  .wordmark__name { font-weight: 700; color: var(--ink); line-height: 1; white-space: nowrap; }

  .card--front .wordmark {
    position: absolute; top: 50%; left: 50%;
    transform: translate(-50%, -50%);
  }
  .card--front .wordmark__name { font-size: 46px; }
  .card--front .wordmark__square { width: 24px; height: 24px; }

  .side-panel {
    position: absolute; top: 0; right: 0;
    width: 200px; height: 100%;
    background: var(--panel);
    border-left: 4px solid var(--rule);
  }

  .card--back .wordmark { position: absolute; left: 40px; top: 110px; }
  .card--back .wordmark__name { font-size: 28px; }

  .contact {
    position: absolute; left: 42px; top: 200px;
    list-style: none; font-size: 15px; line-height: 1.5; color: var(--ink-soft);
  }
  .tagline {
    position: absolute; right: 26px; top: 110px; width: 152px;
    text-align: right; font-size: 15px; font-weight: 700;
    line-height: 1.4; color: var(--ink-soft);
  }
  .card-holder {
    position: absolute; right: 28px; bottom: 32px;
    font-size: 22px; font-weight: 700; color: var(--ink);
  }
</style>
</head>
<body>
  <section class="card card--front" aria-label="Card front">
    <div class="wordmark">
      <span class="wordmark__square"></span>
      <span class="wordmark__name">Brookvane Consulting</span>
    </div>
  </section>

  <section class="card card--back" aria-label="Card back">
    <div class="side-panel"></div>
    <div class="wordmark">
      <span class="wordmark__square"></span>
      <span class="wordmark__name">Brookvane Consulting</span>
    </div>
    <ul class="contact">
      <li>555-218-4930</li>
      <li>darien@brookvaneconsulting.com</li>
      <li>www.brookvaneconsulting.com</li>
    </ul>
    <p class="tagline">Clear Plans,<br>Strong Leaders,<br>Lasting Growth</p>
    <p class="card-holder">Darien</p>
  </section>
</body>
</html>
```